Fastest Work at home Solution for Small Businesses

We need a web page for a product called *BrightReed*
We develop an innovative VPN Appliance (Model-Name ->Reed Alpha) that gives small business the possibility literally setup the possibility for Companies to let their employees work from home.
With our secure appliance we create safe connection between any business and the employee *working at home*
Our Products *Reed Alpha* are rolled out in minutes.
A. Employees can connect directly
B. Work from any location
C. All this without having to change the company firewall
Use case
=======
1. Go to our page
2. Select Product
3. Order
4. Connect to any Switch in the company
5. install software on employees laptop
***** INSTANT Connection ******
Target Market(s)
Businesses
Coding
Coded - Design and coding required
Number of Pages Required
3 page
Font styles to use
Look and feel
Each slider illustrates characteristics of the customer's brand and the style your logo design should communicate.

```html
<!DOCTYPE html>
<html lang="en">
<head>
<meta charset="utf-8">
<title>BrightReed – Fastest Work at home Solution for Small Businesses</title>
<link href="https://fonts.googleapis.com/css2?family=Jost:wght@400;500;600&display=swap" rel="stylesheet">
<style>
:root{
  --navy:#1b36ad;
  --navy-deep:#142c96;
  --footer:#1532a6;
  --footer-bottom:#10267f;
  --sky:#4cc4f4;
  --sky-soft:#6fd0f6;
  --ink:#2b2b33;
  --muted:#4a4a55;
  --line:#c9c9cf;
  --grey-bg:#efeef1;
  --white:#ffffff;
}
*{margin:0;padding:0;box-sizing:border-box}
html,body{width:1200px;height:4874px;overflow:hidden}
body{font-family:'Jost',sans-serif;color:var(--ink);background:var(--white);position:relative}
.abs{position:absolute}
/* header */
.site-header{position:absolute;left:0;top:0;width:1200px;height:130px;background:var(--white)}
.brand{position:absolute;display:flex;align-items:center;gap:12px;font-weight:600;color:var(--navy)}
.brand .mark{background:var(--navy);border-radius:4px}
.site-header .brand{left:112px;top:44px;font-size:38px}
.site-header .brand .mark{width:30px;height:30px}
.nav a{position:absolute;top:56px;font-size:15px;color:#333;text-decoration:none}
.nav a.active{color:var(--navy);font-weight:500}
/* hero */
.hero{position:absolute;left:0;top:130px;width:1200px;height:728px;
  background:linear-gradient(160deg,#6d6a66 0%,#4a4844 40%,#2f3236 70%,#3b4a52 100%)}
.hero-title{position:absolute;left:724px;top:555px;color:var(--white);font-size:32px;line-height:51px;font-weight:400}
.hero-wedge{position:absolute;left:0;top:750px}
/* section headings */
.section-title{position:absolute;left:0;width:1200px;text-align:center;font-weight:500;color:var(--navy)}
.section-title span{color:var(--sky)}
.rule{position:absolute;height:3px;width:44px;background:var(--sky)}
/* products */
.product-art{position:absolute;border-radius:18px}
.product-title{position:absolute;font-size:28px;font-weight:500;color:var(--navy);line-height:34px}
.product-text{position:absolute;width:498px;font-size:14.5px;line-height:31px;color:var(--muted)}
.btn-outline{position:absolute;width:155px;height:53px;border:2px solid var(--sky);border-radius:27px;color:var(--sky);font-size:16px;display:flex;align-items:center;justify-content:center}
.connector{position:absolute;left:0;top:0}
/* banner */
.promo{position:absolute;left:0;top:2115px;width:1200px;height:497px;
  background:linear-gradient(100deg,#1a3cc2 0%,#2a64dc 45%,#4aa8ec 80%,#6cc4f2 100%)}
.promo h2{position:absolute;left:112px;top:108px;font-size:30px;line-height:45px;font-weight:400;color:var(--white)}
.promo p{position:absolute;left:112px;top:220px;width:480px;font-size:14.5px;line-height:31px;color:#e6eeff}
.btn-solid{position:absolute;display:flex;align-items:center;justify-content:center;border-radius:28px;color:var(--white);font-weight:500}
/* steps */
.steps{position:absolute;left:0;top:2612px;width:1200px;height:683px;background:var(--grey-bg)}
.diamond{position:absolute;width:206px;height:206px;border:3px solid var(--line);border-radius:34px;transform:rotate(45deg)}
.step-label{position:absolute;width:220px;text-align:center;font-size:14px;font-weight:500;line-height:21px;color:#222;text-transform:uppercase}
.step-icon{position:absolute}
/* anywhere */
.anywhere-photo{position:absolute;left:0;top:3295px;width:601px;height:470px;
  background:linear-gradient(120deg,#cfd3d6 0%,#8d7e6e 40%,#3b3530 75%,#2a2623 100%)}
.anywhere{position:absolute;left:601px;top:3295px;width:599px;height:470px;background:var(--sky)}
.anywhere h2{position:absolute;left:47px;top:72px;font-size:32px;font-weight:500;color:var(--white)}
.anywhere p{position:absolute;left:47px;top:160px;width:432px;font-size:14.5px;line-height:27.5px;color:var(--white);text-align:justify}
/* faq */
.faq-item{position:absolute;left:198px;width:810px;height:50px;border-radius:25px;background:var(--white);
  box-shadow:0 2px 9px rgba(0,0,0,.13);font-size:16px;color:#333;padding-left:26px;display:flex;align-items:center}
.faq-item .chev{position:absolute;right:16px;top:13px}
/* footer */
.site-footer{position:absolute;left:0;top:4300px;width:1200px;height:380px;background:var(--footer);color:var(--white)}
.site-footer .brand{left:112px;top:80px;font-size:46px;color:var(--white)}
.site-footer .brand .mark{background:var(--white);width:38px;height:38px}
.footer-about{position:absolute;left:112px;top:160px;width:305px;font-size:13.5px;line-height:25px}
.footer-heading{position:absolute;font-size:19px;font-weight:500;letter-spacing:.3px}
.contact-row{position:absolute;left:470px;font-size:13.5px;line-height:23px;padding-left:42px}
.contact-row svg{position:absolute;left:0;top:2px}
.signup-text{position:absolute;left:765px;top:130px;width:340px;font-size:13.5px;line-height:25px}
.signup-input{position:absolute;left:765px;top:194px;width:325px;height:40px;background:var(--white);color:#555;font-size:14px;padding-left:18px;display:flex;align-items:center}
.footer-bottom{position:absolute;left:0;top:4680px;width:1200px;height:194px;background:var(--footer-bottom);color:var(--white)}
.social{position:absolute;top:48px;width:34px;height:34px;border:2px solid var(--white);border-radius:50%}
.copyright{position:absolute;left:0;top:110px;width:1200px;text-align:center;font-size:14.5px}
.page-no{position:absolute;right:38px;top:160px;font-size:15px}
</style>
</head>
<body>

<header class="site-header">
  <div class="brand"><span class="mark"></span>BrightReed</div>
  <nav class="nav">
    <a class="active" style="left:447px">Home</a>
    <a style="left:543px">About Us</a>
    <a style="left:663px">Products</a>
    <a style="left:781px">How it work</a>
    <a style="left:923px">Blog</a>
    <a style="left:1009px">Contact Us</a>
  </nav>
</header>

<section class="hero" role="img" aria-label="Photo of a woman on a sofa working on a laptop while holding a phone, seen from above">
</section>
<h1 class="hero-title">Fastest Work at home<br>Solution for Small Businesses</h1>
<svg class="hero-wedge" width="1200" height="108" viewBox="0 0 1200 108">
  <polygon points="0,108 1200,0 1200,108" fill="#ffffff"/>
  <polygon points="900,108 1200,0 1200,88" fill="var(--sky)"/>
</svg>

<h2 class="section-title" style="top:862px;font-size:42px">Our <span>Products</span></h2>
<div class="rule" style="left:578px;top:930px"></div>

<svg class="connector" width="1200" height="1800" viewBox="0 0 1200 1800" fill="none" stroke="#8a8a95" stroke-width="2" stroke-dasharray="7 7">
  <path d="M300 1295 V1340 Q300 1358 318 1358 H820 Q838 1358 845 1372"/>
  <path d="M878 1650 V1690 Q878 1708 860 1708 H355 Q338 1708 332 1740"/>
</svg>

<div class="product-art" role="img" aria-label="Silver VPN appliance cube with a black display panel showing the date" style="left:185px;top:995px;width:255px;height:290px;background:linear-gradient(150deg,#3a3a3e 0%,#1d1d20 45%,#c9c9cc 55%,#9a9a9e 100%)"></div>
<h3 class="product-title" style="left:500px;top:1002px">Employees can connect directly</h3>
<p class="product-text" style="left:502px;top:1075px">Sed ut perspiciatis unde omnis iste natus error sit voluptatem accusantiu doloremque laudantium, totam rem aperiam, eaque ipsa quae ab illo in vent et quasi architecto beatae vitae dicta sunt explicabo.</p>
<div class="btn-outline" style="left:503px;top:1198px">Read More</div>

<h3 class="product-title" style="left:197px;top:1425px">Work from any location</h3>
<p class="product-text" style="left:199px;top:1497px">Sed ut perspiciatis unde omnis iste natus error sit voluptatem accusantiu doloremque laudantium, totam rem aperiam, eaque ipsa quae ab illo in vent et quasi architecto beatae vitae dicta sunt explicabo.</p>
<div class="btn-outline" style="left:200px;top:1620px">Read More</div>
<div class="product-art" role="img" aria-label="Two blue VPN appliance cubes with black display panels" style="left:720px;top:1350px;width:345px;height:290px;background:linear-gradient(140deg,#1f4fd6 0%,#2b6df0 50%,#1b3fb8 100%)"></div>

<div class="product-art" role="img" aria-label="Isometric illustration of a person working at a desk beside a red firewall shield" style="left:185px;top:1775px;width:210px;height:260px;background:linear-gradient(160deg,#f2c3cb 0%,#d9416b 35%,#6b5ac8 70%,#3d2d8f 100%)"></div>
<h3 class="product-title" style="left:500px;top:1757px">All this without having to change the<br>company firewall</h3>
<div class="rule" style="left:502px;top:1848px"></div>
<p class="product-text" style="left:502px;top:1873px">Sed ut perspiciatis unde omnis iste natus error sit voluptatem accusantiu doloremque laudantium, totam rem aperiam, eaque ipsa quae ab illo in vent et quasi architecto beatae vitae dicta sunt explicabo.</p>
<div class="btn-outline" style="left:503px;top:1995px">Read More</div>

<section class="promo" role="img" aria-label="Blue-tinted photo of a woman sitting on the floor working on a laptop">
  <h2>Sed ut perspiciatis unde<br>iste natus error sit voluptatem accusan</h2>
  <p>Nemo enim ipsam voluptatem quia voluptas sit aspernatur aut odit aut fugit, sed quia consequuntur magni dolores eos qui ratione voluptate ipsam voluptatem &nbsp;sequi nesciunt.</p>
  <div class="btn-solid" style="left:112px;top:335px;width:157px;height:55px;background:var(--sky);font-size:16px">Read More</div>
</section>

<section class="steps">
  <h2 class="section-title" style="top:50px;font-size:36px">GETTING <span>BRIGHTREED WORKING</span></h2>
  <div class="rule" style="left:578px;top:113px"></div>

  <div class="diamond" style="left:135px;top:193px"></div>
  <div class="diamond" style="left:491px;top:193px"></div>
  <div class="diamond" style="left:847px;top:193px"></div>
  <div class="diamond" style="left:317px;top:380px"></div>
  <div class="diamond" style="left:667px;top:380px"></div>

  <svg class="step-icon" style="left:210px;top:228px" width="56" height="56" viewBox="0 0 56 56"><path d="M54 2 L2 22 L24 30 L32 54 Z" fill="var(--navy)"/></svg>
  <svg class="step-icon" style="left:562px;top:226px" width="62" height="62" viewBox="0 0 62 62" fill="none" stroke="var(--navy)" stroke-width="4"><path d="M20 4 H46 L56 14 V58 H20 Z"/><path d="M28 28 H48 M28 38 H48 M28 48 H42"/><path d="M4 30 H10 L14 48 H26" /><circle cx="14" cy="56" r="3" fill="var(--navy)"/></svg>
  <svg class="step-icon" style="left:915px;top:224px" width="62" height="66" viewBox="0 0 62 66" fill="none" stroke="var(--navy)" stroke-width="4"><circle cx="31" cy="14" r="11"/><path d="M31 26 V48 M22 40 L31 49 L40 40"/><path d="M4 40 V58 H58 V40"/><path d="M2 62 H60"/></svg>
  <svg class="step-icon" style="left:390px;top:412px" width="60" height="60" viewBox="0 0 60 60" fill="none" stroke="var(--navy)" stroke-width="4"><rect x="4" y="12" width="44" height="40" rx="4"/><path d="M18 12 V6 H34 V12"/><path d="M32 30 L54 52 M54 40 V52 H42" /></svg>
  <svg class="step-icon" style="left:740px;top:406px" width="66" height="66" viewBox="0 0 66 66" fill="var(--navy)" stroke="var(--navy)" stroke-width="4"><line x1="33" y1="12" x2="33" y2="36"/><line x1="33" y1="36" x2="10" y2="54"/><line x1="33" y1="36" x2="56" y2="54"/><circle cx="33" cy="10" r="8"/><circle cx="33" cy="36" r="6"/><circle cx="10" cy="56" r="8"/><circle cx="56" cy="56" r="8"/></svg>

  <div class="step-label" style="left:128px;top:310px">Go to our page</div>
  <div class="step-label" style="left:484px;top:310px">Order</div>
  <div class="step-label" style="left:840px;top:310px">Install software on<br>employees laptop</div>
  <div class="step-label" style="left:310px;top:497px">Select product</div>
  <div class="step-label" style="left:660px;top:497px">Connect to any switch<br>in the company</div>
</section>

<div class="anywhere-photo" role="img" aria-label="Photo of a woman working at a desktop computer by a window with a cat sitting on the sill"></div>
<section class="anywhere">
  <h2>WORK FROM ANYWHERE</h2>
  <div class="rule" style="left:47px;top:128px;width:48px;background:var(--navy)"></div>
  <p>There are many variations of passages of Lorem Ipsum available, but the majority have suffered alteration in some form, by injected humour, or randomised words which don't look even slightly believable. If you are going to use a passage of Lorem Ipsum, you need to be sure there isn't anything embarrassing hidden in the middle of text.</p>
  <div class="btn-solid" style="left:47px;top:370px;width:152px;height:52px;background:var(--navy);font-size:16px">READ MORE</div>
</section>

<h2 class="section-title" style="top:3818px;font-size:38px">FAQ’S</h2>
<div class="faq-item" style="top:3910px">Sed ut perspiciatis unde omnis iste natus error sit voluptatem accusantiu?<svg class="chev" width="24" height="24" viewBox="0 0 24 24"><circle cx="12" cy="12" r="12" fill="var(--navy)"/><path d="M10 7 L15 12 L10 17" stroke="#fff" stroke-width="2.4" fill="none"/></svg></div>
<div class="faq-item" style="top:3989px">Sed ut perspiciatis unde omnis iste natus error sit voluptatem accusantiu?<svg class="chev" width="24" height="24" viewBox="0 0 24 24"><circle cx="12" cy="12" r="12" fill="var(--navy)"/><path d="M10 7 L15 12 L10 17" stroke="#fff" stroke-width="2.4" fill="none"/></svg></div>
<div class="faq-item" style="top:4068px">Sed ut perspiciatis unde omnis iste natus error sit voluptatem accusantiu?<svg class="chev" width="24" height="24" viewBox="0 0 24 24"><circle cx="12" cy="12" r="12" fill="var(--navy)"/><path d="M10 7 L15 12 L10 17" stroke="#fff" stroke-width="2.4" fill="none"/></svg></div>
<div class="faq-item" style="top:4148px">Sed ut perspiciatis unde omnis iste natus error sit voluptatem accusantiu?<svg class="chev" width="24" height="24" viewBox="0 0 24 24"><circle cx="12" cy="12" r="12" fill="var(--navy)"/><path d="M10 7 L15 12 L10 17" stroke="#fff" stroke-width="2.4" fill="none"/></svg></div>

<footer class="site-footer">
  <div class="brand"><span class="mark"></span>BrightReed</div>
  <p class="footer-about">Sed ut perspiciatis unde omnis iste natus error sit voluptatem accusantium dolorque laudan tium, totam rem aperiam, eaque ipsa quae ab veritatis et quasi &nbsp;architecto beatae</p>

  <div class="footer-heading" style="left:470px;top:80px">CONTACT US</div>
  <div class="contact-row" style="top:128px"><svg width="18" height="24" viewBox="0 0 18 24" fill="none" stroke="#fff" stroke-width="2"><path d="M9 22 C3 14 2 11 2 8 A7 7 0 0 1 16 8 C16 11 15 14 9 22Z"/><circle cx="9" cy="8" r="2.5"/></svg>BrightReed<br>250 ipsam voluptatem<br>quia voluptas</div>
  <div class="contact-row" style="top:218px"><svg width="20" height="20" viewBox="0 0 20 20" fill="none" stroke="#fff" stroke-width="2"><path d="M4 2 L8 2 L9 6 L6.5 8 A11 11 0 0 0 12 13.5 L14 11 L18 12 L18 16 A2 2 0 0 1 16 18 C8 18 2 12 2 4 A2 2 0 0 1 4 2Z"/></svg>Phone :<br>808-555-0142</div>
  <div class="contact-row" style="top:286px"><svg width="22" height="16" viewBox="0 0 22 16" fill="none" stroke="#fff" stroke-width="2"><rect x="1" y="1" width="20" height="14"/><path d="M1 1 L11 9 L21 1"/></svg>Email :<br>info@brightreed.com</div>

  <div class="footer-heading" style="left:765px;top:78px">SIGN UP TO RECEIVE EMAIL</div>
  <p class="signup-text">Excepteur sint occaecat cupidatat non proident, sunt in culpa qui nemo enim ipsam</p>
  <div class="signup-input">Enter Email</div>
  <div class="btn-solid" style="left:765px;top:254px;width:138px;height:40px;border-radius:20px;background:var(--sky);font-size:13.5px">SUBSCRIBE</div>
</footer>

<div class="footer-bottom">
  <span class="social" style="left:515px"></span>
  <span class="social" style="left:559px"></span>
  <span class="social" style="left:603px"></span>
  <span class="social" style="left:647px"></span>
  <p class="copyright">Copyright © BrightReed 2021. All rights reserved. | Privacy Policy</p>
  <span class="page-no">C2</span>
</div>

</body>
</html>
```